holloway paving service

Needs to have phone number 0418259730 and email markholloway@brightmail.com.au.
ABN 62318470915
name mark holloway

For all your concreting solutions
Excavation
Exposed & colour concrete
House & shed slabs
Driveways
Landing & steps

Contact Information for Business Card

ph 0418259730
email markholloway@brightmail.com.au.
ABN 62318470915
name mark holloway

```html
<!DOCTYPE html>
<html lang="en">
<head>
<meta charset="utf-8">
<title>Holloway Paving Service – Business Card</title>
<link href="https://fonts.googleapis.com/css2?family=Montserrat:wght@600&family=Quicksand:wght@400;500;700&family=Varela+Round&display=swap" rel="stylesheet">
<style>
  :root {
    --orange: #f26722;
    --grey: #5e5e5e;
    --ink: #3d3d3d;
    --paper: #ffffff;
    --backdrop: #d8d9da;
  }
  * { margin: 0; padding: 0; box-sizing: border-box; }
  html, body { width: 1200px; height: 1200px; overflow: hidden; }
  body {
    background: var(--backdrop);
    display: flex;
    flex-direction: column;
    align-items: center;
    justify-content: center;
    gap: 60px;
  }
  .card {
    position: relative;
    width: 820px;
    height: 500px;
    overflow: hidden;
    box-shadow: 0 6px 18px rgba(0,0,0,0.15);
  }

  /* Front */
  .card-front { background: var(--paper); }
  .brand {
    position: absolute;
    left: 90px;
    top: 80px;
    display: flex;
    align-items: center;
  }
  .brand-square {
    width: 90px;
    height: 90px;
    background: var(--orange);
  }
  .brand-divider {
    width: 2px;
    height: 150px;
    background: var(--orange);
    margin: 0 32px 0 40px;
  }
  .brand-name {
    font-family: "Montserrat", sans-serif;
    font-weight: 600;
    font-size: 40px;
    line-height: 1.1;
    color: var(--orange);
    text-transform: uppercase;
    letter-spacing: 0.5px;
  }
  .contact {
    position: absolute;
    left: 250px;
    top: 285px;
    font-family: "Varela Round", sans-serif;
  }
  .contact-name {
    font-size: 38px;
    color: var(--orange);
    margin-bottom: 22px;
    letter-spacing: 1px;
  }
  .contact-phone {
    display: flex;
    align-items: center;
    gap: 10px;
    font-family: "Quicksand", sans-serif;
    font-weight: 500;
    font-size: 30px;
    color: var(--orange);
    letter-spacing: 2px;
    margin-bottom: 10px;
  }
  .contact-line {
    font-family: "Quicksand", sans-serif;
    font-size: 24px;
    color: var(--ink);
    letter-spacing: 1px;
    margin-bottom: 8px;
  }
  .front-band {
    position: absolute;
    left: 0; right: 0; bottom: 0;
    height: 26px;
    display: flex;
  }
  .front-band .band-orange { width: 30%; background: var(--orange); }
  .front-band .band-grey { flex: 1; background: var(--grey); }

  /* Back */
  .card-back {
    background: var(--orange);
    color: var(--paper);
    font-family: "Quicksand", sans-serif;
  }
  .back-phone {
    position: absolute;
    left: 150px;
    top: 70px;
    display: flex;
    align-items: center;
    gap: 18px;
    font-size: 58px;
    font-weight: 500;
    letter-spacing: 6px;
  }
  .tagline {
    position: absolute;
    left: 150px;
    top: 165px;
    font-size: 27px;
    font-weight: 700;
    letter-spacing: 1.5px;
  }
  .services {
    position: absolute;
    left: 150px;
    top: 215px;
    list-style: none;
    font-size: 24px;
    line-height: 1.4;
    letter-spacing: 1px;
  }
  .services li { position: relative; }
  .services li::before {
    content: "";
    position: absolute;
    left: -26px;
    top: 14px;
    width: 10px;
    height: 6px;
    background: var(--paper);
  }
  .services li:nth-child(2)::before { left: -40px; }
  .services li:nth-child(3)::before { left: -54px; }
  .services li:nth-child(4)::before { left: -68px; }
  .services li:nth-child(5)::before { left: -82px; }
</style>
</head>
<body>

  <section class="card card-front" aria-label="Business card front">
    <div class="brand">
      <div class="brand-square"></div>
      <div class="brand-divider"></div>
      <div class="brand-name">Holloway Paving<br>Service</div>
    </div>
    <div class="contact">
      <p class="contact-name">Mark Holloway</p>
      <p class="contact-phone">
        <svg width="30" height="30" viewBox="0 0 30 30" aria-hidden="true">
          <circle cx="15" cy="15" r="13" fill="none" stroke="#f26722" stroke-width="2"/>
          <path d="M11 8 q-3 7 2 14 l3 -2 -2 -4 -2 1 q-1.5 -3 0 -6 l2 1 2 -4 z" fill="#f26722"/>
        </svg>
        0418259730
      </p>
      <p class="contact-line">markholloway@brightmail.com.au.</p>
      <p class="contact-line">ABN 62318470915</p>
    </div>
    <div class="front-band">
      <div class="band-orange"></div>
      <div class="band-grey"></div>
    </div>
  </section>

  <section class="card card-back" aria-label="Business card back">
    <p class="back-phone">
      <svg width="54" height="54" viewBox="0 0 30 30" aria-hidden="true">
        <circle cx="15" cy="15" r="13" fill="none" stroke="#ffffff" stroke-width="2"/>
        <path d="M11 8 q-3 7 2 14 l3 -2 -2 -4 -2 1 q-1.5 -3 0 -6 l2 1 2 -4 z" fill="#ffffff"/>
      </svg>
      0418259730
    </p>
    <p class="tagline">For all your concreting solutions:</p>
    <ul class="services">
      <li>Excavation</li>
      <li>Exposed &amp; colour concrete</li>
      <li>House &amp; shed slabs</li>
      <li>Driveways</li>
      <li>Landing &amp; steps</li>
    </ul>
  </section>

</body>
</html>
```